Corvana Tongue Works, LLC

We need a business card that includes information about our business and conveys a reliable business that provides document translation services and interpreters for a variety of corporate and individual clients. We want to come across as professional, reliable, yet approachable. It should include the following on one side:

ESL / ENL Language Classes, Private Lessons, and Online Tutors
PLEXA Training and Testing
Translating & Interpreting Services
Contact us about Over-the-Phone Interpreting in over 200 languages
24/7/365
www.corvanatongue.example

The other side should include (555) 481-3062

Rhoda Pelling, President
482 Garnet Ave., Ste. 219
Indianapolis, IN 40917

Please add USA as part of the address. Also, please add rmpelling@corvanatongueworks.example as the e-mail address. Thank you.

Target Market(s)

Business professionals, their families, the international community

Industry/Entity Type

Business

Contact Information for Business Card

24/7/365
www.corvanatongue.example

(555) 481-3062

Rhoda Pelling, President
482 Garnet Ave., Ste. 219
Indianapolis, IN 40917
USA

Font styles to use
Sans Serif

Colors

Designer to choose colors to be used in the design.

Requirements
Must have
• See project description
• e-mail address and web address
• Phone number
Nice to have
• a globe
• physical address
Should not have
• Should not have the same color scheme as other agencies in our market in Indiana unless it is blue and black. No purple or yellow.

```html
<!DOCTYPE html>
<html lang="en">
<head>
<meta charset="utf-8">
<title>Corvana Tongue Works, LLC — Business Card</title>
<link rel="stylesheet" href="https://fonts.googleapis.com/css2?family=Lato:wght@400;700;900&display=swap">
<style>
  :root{
    --backdrop:#e6e6e4;
    --card:#f4f4f4;
    --ink:#111111;
    --text:#4a4a4a;
    --blue:#2591d6;
    --black:#000000;
    --rule:#c9c9c9;
    --map-a:#dcdcdc;
    --map-b:#e8e8e8;
  }
  *{box-sizing:border-box;margin:0;padding:0}
  html,body{width:1200px;height:960px;overflow:hidden}
  body{background:var(--backdrop);font-family:"Lato",Arial,sans-serif;position:relative}
  .card{position:absolute;width:600px;height:343px;background:var(--card);border-radius:22px;overflow:hidden;box-shadow:0 3px 8px rgba(0,0,0,.25)}
  .card--front{left:302px;top:129px}
  .card--back{left:299px;top:488px}

  /* front */
  .brand-band{position:absolute;left:43px;top:0;width:83px;height:100%;background:linear-gradient(var(--black) 0 36%,var(--blue) 36% 100%)}
  .brand-mark{position:absolute;left:33px;top:117px;width:106px;height:106px;border-radius:50%;background:var(--blue);border:5px solid #fff;box-shadow:0 0 0 3px var(--blue)}
  .brand-name{position:absolute;left:135px;top:132px;font-size:25px;line-height:29px;color:var(--ink);font-weight:400}
  .divider{position:absolute;left:279px;top:96px;width:1px;height:158px;background:var(--rule)}
  .person{position:absolute;left:302px;top:94px}
  .person__name{font-size:22px;font-weight:700;color:var(--blue);letter-spacing:.2px;text-transform:uppercase}
  .person__title{font-size:15px;font-weight:900;color:var(--ink);margin-top:1px;margin-left:2px}
  .contact{list-style:none;margin-top:9px;font-size:14px;color:var(--text);line-height:19px}
  .contact li{display:flex;align-items:flex-start;gap:7px;margin-bottom:6px}
  .contact li.tight{margin-bottom:1px}
  .contact svg{flex:none;width:14px;height:14px;margin-top:2px;fill:var(--blue)}

  /* back */
  .world-map{position:absolute;left:0;top:0;width:100%;height:100%;background:radial-gradient(ellipse at 50% 55%,var(--map-a),var(--map-b) 60%,var(--card) 85%);opacity:.9}
  .services{position:absolute;left:0;width:100%;text-align:center;top:80px;font-size:15px;line-height:19px;color:var(--ink)}
  .callout{position:absolute;left:0;width:100%;text-align:center;top:156px;font-size:17px;line-height:21px;font-weight:900;color:var(--ink);text-transform:uppercase}
  .hours{position:absolute;left:0;width:100%;top:218px;text-align:center;font-size:20px;font-weight:900;color:var(--ink);display:flex;justify-content:center;align-items:center;gap:5px}
  .hours svg{width:19px;height:19px}
  .web{position:absolute;left:0;width:100%;top:246px;text-align:center;font-size:17px;color:var(--blue)}
  .web b{font-weight:900}
</style>
</head>
<body>
  <section class="card card--front" aria-label="Card front">
    <div class="brand-band"></div>
    <div class="brand-mark" aria-hidden="true"></div>
    <p class="brand-name">Corvana<br>Tongue<br>Works, LLC</p>
    <div class="divider"></div>
    <div class="person">
      <h1 class="person__name">Rhoda Pelling</h1>
      <p class="person__title">PRESIDENT</p>
      <ul class="contact">
        <li><svg viewBox="0 0 24 24"><path d="M12 2a7 7 0 0 0-7 7c0 5 7 13 7 13s7-8 7-13a7 7 0 0 0-7-7zm0 9.5A2.5 2.5 0 1 1 12 6.5a2.5 2.5 0 0 1 0 5z"/></svg><span>482 Garnet Ave., Ste. 219<br>Indianapolis, IN 40917</span></li>
        <li class="tight"><svg viewBox="0 0 24 24"><path d="M6.6 10.8a15.1 15.1 0 0 0 6.6 6.6l2.2-2.2a1 1 0 0 1 1-.25 11.4 11.4 0 0 0 3.6.57 1 1 0 0 1 1 1V20a1 1 0 0 1-1 1A17 17 0 0 1 3 4a1 1 0 0 1 1-1h3.5a1 1 0 0 1 1 1c0 1.25.2 2.45.57 3.57a1 1 0 0 1-.25 1z"/></svg><span>(555) 481-3062</span></li>
        <li class="tight"><svg viewBox="0 0 24 24"><path d="M2 5h20v14H2zm2 2v.5l8 5 8-5V7l-8 5z"/></svg><span>rmpelling@corvanatongueworks.example</span></li>
        <li><svg viewBox="0 0 24 24"><circle cx="12" cy="12" r="10"/><path d="M12 2c3 3 3 17 0 20M2 12h20" stroke="#fff" stroke-width="1.6" fill="none"/></svg><span>www.corvanatongue.example</span></li>
      </ul>
    </div>
  </section>

  <section class="card card--back" aria-label="Card back">
    <div class="world-map" role="img" aria-label="Faint world map in light grey behind the text"></div>
    <p class="services">ESL / ENL Language Classes, Private Lessons, &amp; Online Tutors<br>PLEXA Training &amp; Testing<br>Translating &amp; Interpreting Services</p>
    <p class="callout">Contact us about over-the-phone<br>interpreting in over 200 languages</p>
    <p class="hours"><svg viewBox="0 0 24 24" fill="none" stroke="#111" stroke-width="2"><circle cx="12" cy="12" r="9.5"/><path d="M12 7v5l-3 4"/></svg>24/7/365</p>
    <p class="web">www.<b>CORVANATONGUE</b>.example</p>
  </section>
</body>
</html>
```